Marlowby Services Website Design

We have most content but require a professional design. We have a logo already and will need it utilized along with several of the photos from the attached documentation.
First page should have our mission and Vision and the synapsis provided in the word document. Visitors will be prompted to select from one of our 3 divisions from this page.
Each division will have the same list of tabs : About, Services, Safety, Careers and Contact.
Photos on each divisions page should be representative of the divisions offerings. The word doc attached contains the requested content and we are open to edits that would complement and fill the website.
I like the Quorvane site www.quorvane.example - they are our competition so cant be modeled directly after this.
Please include prompts to request quote at each service page. align the format of the geotechnical page to the other 2 divisions.
I used chat gpt for some of the content so will need it optimized for SCO.

```html
<!DOCTYPE html>
<html lang="en">
<head>
<meta charset="utf-8">
<title>Marlowby Services</title>
<link href="https://fonts.googleapis.com/css2?family=Exo+2:wght@500;600;700;800&display=swap" rel="stylesheet">
<style>
:root{
  --red:#ee1d25;
  --ink:#111111;
  --white:#ffffff;
  --grey-band:#6b6e73;
  --footer:#000000;
  --dot:#6a4a3a;
}
*{box-sizing:border-box;margin:0;padding:0}
html,body{width:1200px;height:3141px;overflow:hidden}
body{position:relative;background:var(--white);font-family:"Exo 2",sans-serif;color:var(--ink)}
.abs{position:absolute}
.hero{left:0;top:0;width:1200px;height:600px;background:linear-gradient(180deg,#3a6db8 0%,#6f98cf 18%,#3f4a32 26%,#7b6750 40%,#8c7559 100%)}
.hero-truck{left:95px;top:215px;width:950px;height:355px;background:linear-gradient(180deg,#f2f2f2 0%,#dcdcdc 55%,#2b2b2b 80%,#1a1a1a 100%);border-radius:18px}
.brand{left:112px;top:16px;font-size:38px;font-weight:800;color:var(--red);letter-spacing:2px}
.nav{right:125px;top:26px;display:flex;gap:42px}
.nav a{color:var(--white);text-decoration:none;font-weight:700;font-size:16px}
.sec-title{left:0;width:1200px;text-align:center;font-size:31px;font-weight:800;color:var(--ink)}
.sec-title span{color:var(--red)}
.svc{width:200px;text-align:center}
.svc .ring{width:146px;height:146px;margin:0 auto;border:2px dotted var(--dot);border-radius:50%;display:flex;align-items:center;justify-content:center}
.svc .disc{width:120px;height:120px;border-radius:50%;background:var(--red);display:flex;align-items:center;justify-content:center}
.svc p{margin-top:18px;font-size:15.5px;font-weight:700;line-height:22px}
.photo{background:linear-gradient(180deg,#c9ced4 0%,#b6bcc2 45%,#8d8a82 100%)}
.vision-photo{left:0;top:1234px;width:598px;height:317px;border-radius:0 8px 8px 0}
.vision-box{left:557px;top:1277px;width:531px;height:236px;background:var(--red);border-radius:8px;padding:50px 60px 0 86px;color:var(--white);font-weight:700;font-size:16.5px;line-height:29px}
.mission{left:0;top:1624px;width:1200px;height:492px;background:linear-gradient(180deg,#777a7e,#5f6266)}
.mission .sec-title{color:var(--white);top:68px}
.mission-text{left:112px;top:168px;width:488px;color:var(--white);font-weight:600;font-size:14.5px;line-height:24px;text-align:justify}
.mission-photo{left:643px;top:141px;width:445px;height:282px;border-radius:6px;background:linear-gradient(180deg,#8aa0b8 0%,#e9e9e9 30%,#cfcfcf 60%,#3e3f36 100%)}
.card{width:280px;height:272px;border-bottom:5px solid var(--red);border-radius:6px}
.card-label{width:330px;text-align:center;font-size:20px;font-weight:700;line-height:24px}
.footer{left:0;top:2712px;width:1200px;height:429px;background:var(--footer);color:var(--white)}
.footer .brand{left:113px;top:75px;top:79px}
.foot-about{left:114px;top:160px;width:444px;font-size:14.5px;font-weight:600;line-height:24px;text-align:justify}
.foot-head{font-size:18px;font-weight:700}
.foot-links{left:630px;top:150px}
.foot-links ul{list-style:none;margin:10px 0 0 6px}
.foot-links li{font-size:15px;font-weight:700;line-height:24px}
.foot-contact{left:808px;top:150px}
.contact-row{display:flex;align-items:flex-start;gap:16px;margin-top:14px;font-size:15px;font-weight:700;line-height:23px}
.contact-row svg{flex:none}
.foot-rule{left:96px;top:367px;width:1024px;height:1px;background:#8a8a8a}
.copyright{left:0;width:1200px;top:388px;text-align:center;font-size:15px;font-weight:700}
</style>
</head>
<body>

<header>
  <div class="abs hero" role="img" aria-label="Marlowby aerial access truck parked on a gravel lot under a blue sky">
    <div class="abs hero-truck"></div>
  </div>
  <div class="abs brand">MARLOWBY</div>
  <nav class="abs nav">
    <a href="#">Home</a><a href="#">Services</a><a href="#">Vision</a><a href="#">Mission</a><a href="#">Contact Us</a>
  </nav>
</header>

<section>
  <h2 class="abs sec-title" style="top:680px"><span>Marlowby</span> Services</h2>

  <div class="abs svc" style="left:105px;top:777px">
    <div class="ring"><div class="disc">
      <svg width="60" height="60" viewBox="0 0 60 60" fill="none" stroke="#fff" stroke-width="2.5"><path d="M8 30h24v14H8zM8 30l4-6h16l4 6M20 24v20M4 48h34"/><path d="M40 12l10 4v8c0 6-4 10-10 12-6-2-10-6-10-12v-8z"/><path d="M35 23l4 4 7-7"/></svg>
    </div></div>
    <p>Delivering<br>safe</p>
  </div>

  <div class="abs svc" style="left:304px;top:839px">
    <div class="ring"><div class="disc">
      <svg width="60" height="60" viewBox="0 0 60 60" fill="none" stroke="#fff" stroke-width="2.5"><circle cx="30" cy="30" r="14"/><path d="M30 8v6M30 46v6M8 30h6M46 30h6M14 14l4 4M42 42l4 4M46 14l-4 4M18 42l-4 4"/><path d="M26 22v10l4 4 4-4V22"/></svg>
    </div></div>
    <p>reliable aerial<br>access and maintenance<br>services to Oil&amp;Gas,</p>
  </div>

  <div class="abs svc" style="left:510px;top:777px">
    <div class="ring"><div class="disc">
      <svg width="60" height="60" viewBox="0 0 60 60" fill="none" stroke="#fff" stroke-width="2.5"><path d="M14 46a16 16 0 0 1 32 0zM10 46h40M30 30v-6"/><path d="M14 8v20M10 8h8M44 12a5 5 0 1 0 0.1 0M44 17v13"/></svg>
    </div></div>
    <p>Construction</p>
  </div>

  <div class="abs svc" style="left:704px;top:839px">
    <div class="ring"><div class="disc">
      <svg width="60" height="60" viewBox="0 0 60 60" fill="none" stroke="#fff" stroke-width="2.5"><circle cx="30" cy="30" r="20"/><path d="M22 40l12-12a6 6 0 1 0-4-4L18 36z"/></svg>
    </div></div>
    <p>Utility</p>
  </div>

  <div class="abs svc" style="left:896px;top:777px">
    <div class="ring"><div class="disc">
      <svg width="60" height="60" viewBox="0 0 60 60" fill="none" stroke="#fff" stroke-width="2.5"><path d="M8 50V28l12-8v8l12-8v8l12-8v30zM4 50h52"/><path d="M16 20V10M16 12c-4 0-6-3-6-6 4 0 6 3 6 6zM16 12c4 0 6-3 6-6-4 0-6 3-6 6z"/><circle cx="30" cy="40" r="5"/></svg>
    </div></div>
    <p>Renewable energy<br>industries</p>
  </div>
</section>

<section>
  <h2 class="abs sec-title" style="top:1148px"><span>Our</span> Vision</h2>
  <div class="abs photo vision-photo" role="img" aria-label="Two aerial access trucks on a gravel pad beside wind turbines"></div>
  <div class="abs vision-box">To be the leading provider of aerial access, geotechnical drilling, and service solutions, setting the standard for excellence in safety, efficiency, and environmental stewardship.</div>
</section>

<section class="abs mission">
  <h2 class="abs sec-title"><span style="color:var(--red)">Our</span> Mission</h2>
  <p class="abs mission-text">At Marlowby, our mission is to deliver unparalleled aerial access, geotechnical drilling, and service and maintenance solutions, consistently exceeding our clients' expectations. We strive to achieve this by investing in cutting-edge technology, fostering a culture of safety and continuous improvement, and prioritizing environmental sustainability. Through collaboration, integrity, and dedication, we aim to contribute to the success of our clients while maintaining the highest standards of quality and professionalism.</p>
  <div class="abs mission-photo" role="img" aria-label="Aerial view of a Marlowby boom truck in a yard"></div>
</section>

<section>
  <h2 class="abs sec-title" style="top:2189px"><span>Select</span> Division</h2>
  <div class="abs card" style="left:135px;top:2301px;background:linear-gradient(180deg,#9aa3a8,#6d7276 60%,#8a8f8c)" role="img" aria-label="Aerial access boom raising a banner over a small town"></div>
  <div class="abs card" style="left:460px;top:2301px;background:linear-gradient(180deg,#2f6fd0 0%,#5c93e2 45%,#bfbfbf 70%,#8b7d64 100%)" role="img" aria-label="Geotechnical drilling truck under a clear blue sky"></div>
  <div class="abs card" style="left:785px;top:2301px;background:linear-gradient(180deg,#1f5fd0,#4f8ee6 60%,#9cc0ee)" role="img" aria-label="Boom reaching up to a wind turbine blade"></div>
  <div class="abs card-label" style="left:99px;top:2605px">Aerial Access</div>
  <div class="abs card-label" style="left:437px;top:2605px">Geotechnical Drilling</div>
  <div class="abs card-label" style="left:757px;top:2605px">Renewable Energy<br>Services</div>
</section>

<footer class="abs footer">
  <div class="abs brand">MARLOWBY</div>
  <p class="abs foot-about">At Marlowby, we understand that the key to harnessing the full potential of wind energy lies in the meticulous maintenance of your wind turbines. Our commitment to excellence and unwavering focus on routine maintenance positions us as your dedicated partner in ensuring optimal turbine performance and longevity.</p>
  <div class="abs foot-links">
    <div class="foot-head">Quick Links</div>
    <ul><li>Home</li><li>Services</li><li>Vision</li><li>Mission</li><li>Contact Us</li></ul>
  </div>
  <div class="abs foot-contact">
    <div class="foot-head">Contact Us</div>
    <div class="contact-row">
      <svg width="30" height="30" viewBox="0 0 30 30"><circle cx="15" cy="15" r="15" fill="#fff"/><path d="M15 7a5 5 0 0 0-5 5c0 4 5 10 5 10s5-6 5-10a5 5 0 0 0-5-5z" fill="none" stroke="#555" stroke-width="1.3"/><circle cx="15" cy="12" r="1.8" fill="none" stroke="#555" stroke-width="1.3"/></svg>
      <span>118 Ridgeline Road Elmsford<br>AB T0X-4B0</span>
    </div>
    <div class="contact-row">
      <svg width="30" height="30" viewBox="0 0 30 30"><circle cx="15" cy="15" r="15" fill="#fff"/><rect x="8" y="10" width="14" height="10" fill="none" stroke="#555" stroke-width="1.3"/><path d="M8 10l7 6 7-6" fill="none" stroke="#555" stroke-width="1.3"/></svg>
      <span style="padding-top:3px">info@marlowbyservices.example</span>
    </div>
  </div>
  <div class="abs foot-rule"></div>
  <p class="abs copyright">Copyright © 2024 MARLOWBY. All rights reserved.</p>
</footer>

</body>
</html>
```